Etiketten-Design für Kräuterbonbon-Metalldose
Katrin Wolber hat sehr viel Talent. Das Design ist absolut kreativ.
Zielgruppe
Unsere Firma FelvoNat verkauft verschiedene Sorten Kräuterbonbons.
Wir brauchen ein Etikett, dass auf eine Metall-Dose (Durchmesser 10 cam, Höhe ca. 3 cm) geklebt wird.
Zielgruppe: jung-alt
Aufgabenstellung
Der Name unserer Kräuterbonbons ist Moospille.
Wir möchten, dass unsere Kunden, wenn sie das Etikett sehen einen Bezug zur Schweiz herstellen können.
Wir verwenden für unsere Bonbons unterschiedliche Kräuter für verschiedene Anwendungen:
Konkret sind erstmal 4 Dosen geplant:
-Kräutermischung aus 16 Kräuter gegen Husten
-Salbei gegen Halsschmerzen
-Anis gegen Magenschmerzen
-Zitrone/Ingwer für die Nerven
Vorderseite: Produktbeschreibung
Rückseite: unsere Herstellerangaben
Größenangaben der Dose: Durchmesser 10 cm, Höhe ca. 3 cm
Im Anhang habe ich Ihnen noch weitere/ genauere Informationen zur Verfügung bereitgestellt!

```html
<!DOCTYPE html>
<html lang="de">
<head>
<meta charset="utf-8">
<title>Moospille – Schweizer Kräuterbonbon Etiketten</title>
<link rel="stylesheet" href="https://fonts.googleapis.com/css2?family=Fira+Sans+Condensed:wght@500;600&family=Open+Sans:wght@700&display=swap">
<style>
  :root {
    --paper: #ffffff;
    --rim: #d9dbdd;
    --rim-edge: #eef0f1;
    --inner: #e9ebec;
    --white: #ffffff;
    --tone-cough: #8fbd4f;
    --tone-sage: #8a6cab;
    --tone-anise: #7c8a47;
    --tone-ginger: #e2a23c;
  }
  html, body {
    margin: 0;
    width: 1200px;
    height: 1200px;
    overflow: hidden;
    background: var(--paper);
  }
  .label-sheet {
    display: grid;
    grid-template-columns: 600px 600px;
    grid-template-rows: 600px 600px;
    width: 1200px;
    height: 1200px;
  }
  .label {
    display: flex;
    align-items: center;
    justify-content: center;
  }
  .label svg { width: 500px; height: 500px; display: block; }
  .label--cough  { --tone: var(--tone-cough); }
  .label--sage   { --tone: var(--tone-sage); }
  .label--anise  { --tone: var(--tone-anise); }
  .label--ginger { --tone: var(--tone-ginger); }

  .rim { fill: var(--rim); stroke: var(--rim-edge); stroke-width: 4; }
  .ring { fill: var(--tone); }
  .inner { fill: var(--inner); }
  .tab { fill: var(--tone); }
  .brand {
    font-family: "Open Sans", sans-serif;
    font-weight: 700;
    font-size: 34px;
    fill: var(--white);
  }
  .claim {
    font-family: "Open Sans", sans-serif;
    font-weight: 700;
    font-size: 17px;
    letter-spacing: 2px;
    fill: var(--white);
    opacity: 0.9;
  }
  .tab-text {
    font-family: "Fira Sans Condensed", sans-serif;
    font-weight: 600;
    font-size: 22px;
    fill: var(--white);
  }
  .tab-text .small { font-size: 11px; font-weight: 500; }
  .title {
    font-family: "Fira Sans Condensed", sans-serif;
    font-weight: 600;
    font-size: 33px;
    fill: var(--tone);
  }
  .title--compact { font-size: 29px; }
  .sprig { fill: var(--tone); opacity: 0.85; }
  .ornament { fill: var(--white); opacity: 0.55; }
</style>
</head>
<body>
<main class="label-sheet">

  <section class="label label--cough">
    <svg viewBox="0 0 500 500" aria-label="Etikett Kräutermischung gegen Husten">
      <defs>
        <linearGradient id="herb-cough" x1="0" y1="0" x2="0" y2="1">
          <stop offset="0" stop-color="#9cc46a"/><stop offset="1" stop-color="#3f7a2c"/>
        </linearGradient>
        <path id="arc-top-cough" d="M 57,250 A 193,193 0 0 1 443,250"/>
        <path id="arc-bottom-cough" d="M 30,250 A 220,220 0 0 0 470,250"/>
      </defs>
      <circle class="rim" cx="250" cy="250" r="247"/>
      <circle class="ring" cx="250" cy="250" r="234"/>
      <circle class="inner" cx="250" cy="250" r="178"/>
      <text class="brand"><textPath href="#arc-top-cough" startOffset="50%" text-anchor="middle">Moospille</textPath></text>
      <text class="claim"><textPath href="#arc-bottom-cough" startOffset="50%" text-anchor="middle">Schweizer Kräuterbonbon</textPath></text>
      <ellipse class="ornament" role="img" aria-label="Zweig-Ornament" cx="98" cy="138" rx="14" ry="7" transform="rotate(-35 98 138)"/>
      <ellipse class="ornament" role="img" aria-label="Zweig-Ornament" cx="402" cy="138" rx="14" ry="7" transform="rotate(35 402 138)"/>
      <ellipse class="sprig" role="img" aria-label="Kräuterzweig-Symbol" cx="250" cy="112" rx="10" ry="30"/>
      <text class="title title--compact" text-anchor="middle">
        <tspan x="250" y="182">Kräutermischung</tspan>
        <tspan x="250" y="216">aus 16 Kräuter</tspan>
        <tspan x="250" y="250">gegen Husten</tspan>
      </text>
      <rect class="tab" x="48" y="222" width="82" height="56" rx="28"/>
      <text class="tab-text" x="88" y="258" text-anchor="middle">125G</text>
      <rect class="tab" x="370" y="222" width="84" height="56" rx="28"/>
      <text class="tab-text" x="410" y="258" text-anchor="middle">16 <tspan class="small">pieces</tspan></text>
      <ellipse role="img" aria-label="Illustration von Petersilie und Kräuterbündel" cx="250" cy="345" rx="62" ry="58" fill="url(#herb-cough)"/>
    </svg>
  </section>

  <section class="label label--sage">
    <svg viewBox="0 0 500 500" aria-label="Etikett Salbei gegen Halsschmerzen">
      <defs>
        <linearGradient id="herb-sage" x1="0" y1="0" x2="0" y2="1">
          <stop offset="0" stop-color="#a48fcf"/><stop offset="1" stop-color="#5d7a5a"/>
        </linearGradient>
        <path id="arc-top-sage" d="M 57,250 A 193,193 0 0 1 443,250"/>
        <path id="arc-bottom-sage" d="M 30,250 A 220,220 0 0 0 470,250"/>
      </defs>
      <circle class="rim" cx="250" cy="250" r="247"/>
      <circle class="ring" cx="250" cy="250" r="234"/>
      <circle class="inner" cx="250" cy="250" r="178"/>
      <text class="brand"><textPath href="#arc-top-sage" startOffset="50%" text-anchor="middle">Moospille</textPath></text>
      <text class="claim"><textPath href="#arc-bottom-sage" startOffset="50%" text-anchor="middle">Schweizer Kräuterbonbon</textPath></text>
      <ellipse class="ornament" role="img" aria-label="Zweig-Ornament" cx="98" cy="138" rx="14" ry="7" transform="rotate(-35 98 138)"/>
      <ellipse class="ornament" role="img" aria-label="Zweig-Ornament" cx="402" cy="138" rx="14" ry="7" transform="rotate(35 402 138)"/>
      <ellipse class="sprig" role="img" aria-label="Kräuterzweig-Symbol" cx="250" cy="112" rx="10" ry="30"/>
      <text class="title" text-anchor="middle">
        <tspan x="250" y="205">Salbei gegen</tspan>
        <tspan x="250" y="258">Halsschmerzen</tspan>
      </text>
      <rect class="tab" x="48" y="222" width="82" height="56" rx="28"/>
      <text class="tab-text" x="88" y="258" text-anchor="middle">125G</text>
      <rect class="tab" x="370" y="222" width="84" height="56" rx="28"/>
      <text class="tab-text" x="410" y="258" text-anchor="middle">16 <tspan class="small">pieces</tspan></text>
      <ellipse role="img" aria-label="Illustration einer blühenden Salbeipflanze" cx="250" cy="345" rx="58" ry="62" fill="url(#herb-sage)"/>
    </svg>
  </section>

  <section class="label label--anise">
    <svg viewBox="0 0 500 500" aria-label="Etikett Anis gegen Magenschmerzen">
      <defs>
        <linearGradient id="herb-anise" x1="0" y1="0" x2="0" y2="1">
          <stop offset="0" stop-color="#7f9660"/><stop offset="1" stop-color="#4d6438"/>
        </linearGradient>
        <path id="arc-top-anise" d="M 57,250 A 193,193 0 0 1 443,250"/>
        <path id="arc-bottom-anise" d="M 30,250 A 220,220 0 0 0 470,250"/>
      </defs>
      <circle class="rim" cx="250" cy="250" r="247"/>
      <circle class="ring" cx="250" cy="250" r="234"/>
      <circle class="inner" cx="250" cy="250" r="178"/>
      <text class="brand"><textPath href="#arc-top-anise" startOffset="50%" text-anchor="middle">Moospille</textPath></text>
      <text class="claim"><textPath href="#arc-bottom-anise" startOffset="50%" text-anchor="middle">Schweizer Kräuterbonbon</textPath></text>
      <ellipse class="ornament" role="img" aria-label="Zweig-Ornament" cx="98" cy="138" rx="14" ry="7" transform="rotate(-35 98 138)"/>
      <ellipse class="ornament" role="img" aria-label="Zweig-Ornament" cx="402" cy="138" rx="14" ry="7" transform="rotate(35 402 138)"/>
      <ellipse class="sprig" role="img" aria-label="Kräuterzweig-Symbol" cx="250" cy="112" rx="10" ry="30"/>
      <text class="title" text-anchor="middle">
        <tspan x="250" y="212">Anis gegen</tspan>
        <tspan x="250" y="258" style="font-size:28px">Magenschmerzen</tspan>
      </text>
      <rect class="tab" x="48" y="222" width="82" height="56" rx="28"/>
      <text class="tab-text" x="88" y="258" text-anchor="middle">125G</text>
      <rect class="tab" x="370" y="222" width="84" height="56" rx="28"/>
      <text class="tab-text" x="410" y="258" text-anchor="middle">16 <tspan class="small">pieces</tspan></text>
      <ellipse role="img" aria-label="Illustration eines Anis-Zweigs mit Blüten und Sternanis" cx="250" cy="348" rx="64" ry="60" fill="url(#herb-anise)"/>
    </svg>
  </section>

  <section class="label label--ginger">
    <svg viewBox="0 0 500 500" aria-label="Etikett Zitrone und Ingwer für die Nerven">
      <defs>
        <linearGradient id="herb-ginger" x1="0" y1="0" x2="0" y2="1">
          <stop offset="0" stop-color="#d6b68a"/><stop offset="0.5" stop-color="#6aa048"/><stop offset="1" stop-color="#f2d64a"/>
        </linearGradient>
        <path id="arc-top-ginger" d="M 57,250 A 193,193 0 0 1 443,250"/>
        <path id="arc-bottom-ginger" d="M 30,250 A 220,220 0 0 0 470,250"/>
      </defs>
      <circle class="rim" cx="250" cy="250" r="247"/>
      <circle class="ring" cx="250" cy="250" r="234"/>
      <circle class="inner" cx="250" cy="250" r="178"/>
      <text class="brand"><textPath href="#arc-top-ginger" startOffset="50%" text-anchor="middle">Moospille</textPath></text>
      <text class="claim"><textPath href="#arc-bottom-ginger" startOffset="50%" text-anchor="middle">Schweizer Kräuterbonbon</textPath></text>
      <ellipse class="ornament" role="img" aria-label="Zweig-Ornament" cx="98" cy="138" rx="14" ry="7" transform="rotate(-35 98 138)"/>
      <ellipse class="ornament" role="img" aria-label="Zweig-Ornament" cx="402" cy="138" rx="14" ry="7" transform="rotate(35 402 138)"/>
      <ellipse class="sprig" role="img" aria-label="Kräuterzweig-Symbol" cx="250" cy="112" rx="10" ry="30"/>
      <text class="title" text-anchor="middle">
        <tspan x="250" y="212">Zitrone/Ingwer</tspan>
        <tspan x="250" y="258">für die Nerven</tspan>
      </text>
      <rect class="tab" x="48" y="222" width="82" height="56" rx="28"/>
      <text class="tab-text" x="88" y="258" text-anchor="middle">125G</text>
      <rect class="tab" x="370" y="222" width="84" height="56" rx="28"/>
      <text class="tab-text" x="410" y="258" text-anchor="middle">16 <tspan class="small">pieces</tspan></text>
      <ellipse role="img" aria-label="Illustration von Ingwerwurzel, Blättern und halbierter Zitrone" cx="250" cy="348" rx="64" ry="58" fill="url(#herb-ginger)"/>
    </svg>
  </section>

</main>
</body>
</html>
```